Marwick Family Chiropractic Stationary

The letterhead and business card must have our logo.
We would like to see the logo used in different ways ( It can be expanded upon in the stationary.)
Please use the the same or similar colors.
Must be eye catching and memorable.
Must be easy to read

Reason: The doctor has been too busy to make any final decisions. He would like to give himself a little more time.

Target Market(s)

Chiropractic Healthcare

Industry/Entity Type

Business

Requirements
Must have
• Dr. Leonard Marwick D.C.
Chiropractor

860-555-0183

417 Birchfield Road, 2nd Floor
Vernon, CT 06091

drmarwick@marwickspine.example
www.marwickspine.example
www.facebook.com/MarwickFamilySpine
Should not have
• should not be difficult to read

```html
<!DOCTYPE html>
<html lang="en">
<head>
<meta charset="utf-8">
<title>Marwick Family Chiropractic – Business Card</title>
<link rel="stylesheet" href="https://fonts.googleapis.com/css2?family=Montserrat:wght@700&family=Open+Sans:ital,wght@0,400;0,600;1,700&display=swap">
<style>
  :root {
    --stage: #8c6a48;
    --card-white: #ffffff;
    --card-brown: #231c15;
    --card-black: #0a0a0a;
    --green: #239a48;
    --lime: #a9cf5a;
    --ink: #2b2b2b;
    --label: #1e1a16;
    --faint: rgba(120, 105, 80, 0.22);
    --shadow: 0 6px 14px rgba(0, 0, 0, 0.45);
  }
  * { margin: 0; padding: 0; box-sizing: border-box; }
  html, body { width: 1200px; height: 788px; overflow: hidden; }
  body {
    position: relative;
    background: var(--stage);
    font-family: "Open Sans", Arial, sans-serif;
  }
  .side-label {
    position: absolute;
    width: 200px;
    text-align: center;
    font-size: 21px;
    color: var(--label);
  }
  .card {
    position: absolute;
    width: 525px;
    height: 300px;
    border-radius: 22px;
    box-shadow: var(--shadow);
    overflow: hidden;
    text-align: center;
  }
  .card--white { background: var(--card-white); }
  .card--brown { background: var(--card-brown); }
  .card--black { background: var(--card-black); }

  .brand-dot {
    position: absolute;
    left: 50%;
    border-radius: 50%;
    transform: translateX(-50%);
  }
  .brand-name {
    position: absolute;
    left: 0; right: 0;
    font-family: "Montserrat", Arial, sans-serif;
    font-weight: 700;
    line-height: 1;
  }
  .brand-name .sub { display: block; }

  .contact {
    position: absolute;
    left: 0; right: 0;
    font-size: 12.5px;
    color: var(--ink);
    line-height: 20px;
  }
  .contact .doctor {
    font-size: 15px;
    font-weight: 600;
    color: var(--green);
  }
  .contact .doctor small { font-size: 12.5px; color: var(--ink); }
  .contact b { font-style: italic; font-weight: 700; }
  .web {
    position: absolute;
    left: 0; right: 0;
    font-size: 15px;
  }
</style>
</head>
<body>

  <div class="side-label" style="left:220px; top:34px;">Front</div>
  <div class="side-label" style="left:786px; top:34px;">Back - 1</div>
  <div class="side-label" style="left:216px; top:404px;">Back - 2</div>
  <div class="side-label" style="left:786px; top:404px;">Back - 3</div>

  <!-- Front -->
  <section class="card card--white" style="left:60px; top:80px;">
    <div class="brand-dot" style="top:28px; width:70px; height:70px; background:var(--green);"></div>
    <div class="brand-name" style="top:110px; color:var(--green); font-size:30px;">
      MARWICK<span class="sub" style="font-size:11px; margin-top:5px;">FAMILY CHIROPRACTIC</span>
    </div>
    <div class="contact" style="top:197px;">
      <p class="doctor">Dr. Leonard Marwick D.C., <small>Chiropractor</small></p>
      <p><b>phone</b> 860-555-0183 &nbsp;|&nbsp; <b>email</b> drmarwick@marwickspine.example</p>
      <p><b>web</b> : www.marwickspine.example &nbsp;|&nbsp; <b>face book</b> : MarwickFamilySpine</p>
      <p>417 Birchfield Road, 2nd Floor, Vernon, CT 06091</p>
    </div>
  </section>

  <!-- Back 1 -->
  <section class="card card--white" style="left:622px; top:74px;">
    <div class="brand-dot" style="top:40px; width:100px; height:100px; background:var(--green);"></div>
    <div class="brand-name" style="top:170px; color:var(--green); font-size:34px;">
      MARWICK<span class="sub" style="font-size:13px; margin-top:6px;">FAMILY CHIROPRACTIC</span>
    </div>
    <p class="web" style="top:259px; color:var(--ink);">www.marwickspine.example</p>
  </section>

  <!-- Back 2 -->
  <section class="card card--brown" style="left:53px; top:445px;">
    <div class="brand-dot" role="img" aria-label="Faint brand circle decoration" style="top:30px; width:210px; height:210px; background:var(--faint);"></div>
    <div class="brand-name" style="top:98px; color:var(--green); font-size:60px;">
      MARWICK<span class="sub" style="font-size:27px; margin-top:12px;">FAMILY CHIROPRACTIC</span>
    </div>
    <p class="web" style="top:261px; color:#ffffff;">www.marwickspine.example</p>
  </section>

  <!-- Back 3 -->
  <section class="card card--black" style="left:622px; top:445px;">
    <div class="brand-dot" style="top:32px; width:110px; height:110px; background:var(--lime);"></div>
    <div class="brand-name" style="top:172px; color:var(--lime); font-size:32px;">
      MARWICK<span class="sub" style="font-size:13px; margin-top:6px;">FAMILY CHIROPRACTIC</span>
    </div>
    <p class="web" style="top:261px; color:#ffffff;">www.marwickspine.example</p>
  </section>

</body>
</html>
```